Maple Grove Schools | brand new stationery!

We need stationery design with our new logo! Our company updated it's name and image and we like to incorporate the new one on our stationery, business cards and email signature. We are looking for fresh, new ideas!
Industry: Childcare, Elementary and Middle School
Company Name: Maple Grove Schools
Tagline: Bright Futures Start Here
Main colors: Blue, white and a little yellow
Star shape is something new for us! Do you see a way to incorporate it as a design element?

```html
<!DOCTYPE html>
<html lang="en">
<head>
<meta charset="utf-8">
<title>Maple Grove Schools — Stationery</title>
<link rel="stylesheet" href="https://fonts.googleapis.com/css2?family=Poppins:wght@400;600;700&family=Open+Sans:wght@400;600&display=swap">
<style>
  :root {
    --navy: #323670;
    --yellow: #e5b025;
    --paper: #f4f4f4;
    --backdrop: #e7e7e7;
    --ink: #2a2a2a;
    --body-ink: #555;
  }
  * { margin: 0; padding: 0; box-sizing: border-box; }
  html, body { width: 1200px; height: 795px; overflow: hidden; }
  body { background: var(--backdrop); position: relative; font-family: "Open Sans", sans-serif; }
  .sheet { position: absolute; background: var(--paper); overflow: hidden; }
  .sheet svg.shape { position: absolute; left: 0; top: 0; }
  .brand { position: absolute; text-align: center; font-family: "Poppins", sans-serif; font-weight: 600; color: var(--ink); line-height: 1.05; }
  .brand-dot { display: block; margin: 0 auto; border-radius: 50%; background: var(--navy); }
  .tagline { position: absolute; font-family: "Poppins", sans-serif; font-weight: 600; color: var(--navy); letter-spacing: 0.08em; white-space: nowrap; }
  .footer-text { position: absolute; color: #fff; font-family: "Open Sans", sans-serif; }
  .icon { display: inline-block; vertical-align: -1px; margin-right: 2px; }

  /* Letterhead */
  .letterhead { left: 293px; top: 99px; width: 292px; height: 415px; }
  .letterhead .brand { left: 10px; top: 20px; width: 108px; font-size: 12px; }
  .letterhead .brand-dot { width: 16px; height: 16px; margin-bottom: 5px; }
  .letterhead .tagline { left: 28px; top: 79px; font-size: 4.8px; }
  .letter-body { position: absolute; left: 27px; top: 126px; width: 240px; font-size: 5.2px; line-height: 8px; color: var(--body-ink); text-align: justify; }
  .letter-body p { margin-bottom: 7.5px; }
  .letterhead .contacts { left: 27px; top: 374px; font-size: 6.2px; line-height: 8.6px; }
  .letterhead .address { right: 25px; top: 383px; font-size: 6.2px; line-height: 8.2px; text-align: right; }

  /* Folder */
  .folder { left: 637px; top: 80px; width: 345px; height: 437px; }
  .folder .brand { left: 40px; top: 160px; width: 265px; font-size: 28px; line-height: 1.08; }
  .folder .brand-dot { width: 48px; height: 48px; margin-bottom: 14px; }
  .folder .tagline { left: 0; width: 345px; text-align: center; top: 399px; font-size: 10.5px; color: var(--yellow); letter-spacing: 0.04em; font-weight: 700; }

  /* Business cards */
  .card-front { left: 187px; top: 550px; width: 132px; height: 75px; }
  .card-front .person { position: absolute; left: 9px; top: 10px; font-family: "Poppins", sans-serif; }
  .card-front .person-name { font-size: 4.6px; font-weight: 700; color: var(--navy); }
  .card-front .person-role { font-size: 3.6px; color: var(--yellow); }
  .card-front .brand { left: 72px; top: 6px; width: 56px; font-size: 7px; }
  .card-front .brand-dot { width: 8px; height: 8px; margin-bottom: 3px; }
  .card-front .tagline { left: 79px; top: 39px; font-size: 2.5px; }
  .card-front .contacts { left: 9px; top: 55px; font-size: 3.4px; line-height: 5px; }
  .card-front .address { right: 9px; top: 60px; font-size: 3.4px; line-height: 5px; text-align: right; }
  .card-back { left: 187px; top: 646px; width: 132px; height: 75px; background: var(--navy); }

  /* DL envelope front */
  .envelope-front { left: 353px; top: 561px; width: 328px; height: 157px; }
  .envelope-front .brand { left: 12px; top: 16px; width: 80px; font-size: 11px; }
  .envelope-front .brand-dot { width: 14px; height: 14px; margin-bottom: 4px; }
  .envelope-front .tagline { left: 23px; top: 64px; font-size: 4.3px; }
  .envelope-front .address { left: 22px; top: 120px; font-size: 6.2px; line-height: 7.4px; }

  /* Envelope back */
  .envelope-back { left: 713px; top: 561px; width: 329px; height: 157px; }
  .envelope-back .brand { left: 104px; top: 10px; width: 120px; font-size: 9px; color: #fff; }
  .envelope-back .brand-dot { width: 12px; height: 12px; margin-bottom: 4px; background: #fff; }
</style>
</head>
<body>

<!-- Letterhead -->
<section class="sheet letterhead">
  <svg class="shape" width="292" height="415" viewBox="0 0 292 415">
    <path d="M0 328 Q150 400 292 352 V415 H0 Z" fill="var(--navy)"/>
    <path d="M85 356 Q190 386 292 346" fill="none" stroke="#fff" stroke-width="3"/>
    <path d="M85 353 Q190 381 292 341" fill="none" stroke="var(--yellow)" stroke-width="3"/>
  </svg>
  <div class="brand"><span class="brand-dot"></span>Maple Grove<br>Schools</div>
  <div class="tagline">Bright Futures Start Here</div>
  <div class="letter-body">
    <p>Dear customer,</p>
    <p>Lorem ipsum dolor sit amet, consectetur adipisicing elit, sed do eiusmod tempor incididunt ut labore et dolore magna aliqua. Ut enim ad minim veniam, quis nostrud exercitation ullamco laboris nisi ut aliquip ex ea commodo consequat. Duis aute irure dolor in reprehenderit in voluptate velit esse cillum dolore eu fugiat nulla pariatur. Excepteur sint occaecat cupidatat non proident, sunt in culpa qui officia deserunt mollit anim id est laborum.</p>
    <p>Lorem ipsum dolor sit amet, consectetur adipisicing elit, sed do eiusmod tempor incididunt ut labore et dolore magna aliqua. Ut enim ad minim veniam, quis nostrud exercitation ullamco laboris nisi ut aliquip ex ea commodo consequat. Duis aute irure dolor in reprehenderit in voluptate velit esse cillum dolore eu fugiat nulla pariatur. Excepteur sint occaecat cupidatat non proident, sunt in culpa qui officia deserunt mollit anim id est laborum.</p>
    <p>Lorem ipsum dolor sit amet, consectetur adipisicing elit, sed do eiusmod tempor incididunt ut labore et dolore magna aliqua. Ut enim ad minim veniam, quis nostrud exercitation ullamco laboris nisi ut aliquip ex ea commodo consequat. Duis aute irure dolor in reprehenderit in voluptate velit esse cillum dolore eu fugiat nulla pariatur. Excepteur sint occaecat cupidatat non proident, sunt in culpa qui officia deserunt mollit anim id est laborum.</p>
  </div>
  <div class="footer-text contacts">
    <div><svg class="icon" width="6" height="6" viewBox="0 0 10 10"><path d="M2 1 L4 3 L3 4.5 Q4.5 6.5 5.5 7 L7 6 L9 8 L7.5 9.5 Q3 9 0.5 2.5 Z" fill="var(--yellow)"/></svg>(555) 014-2290</div>
    <div><svg class="icon" width="6" height="6" viewBox="0 0 10 10"><rect x="0.5" y="2" width="9" height="6" fill="none" stroke="var(--yellow)"/><path d="M0.5 2 L5 5.5 L9.5 2" fill="none" stroke="var(--yellow)"/></svg>info@maplegrove-schools.com</div>
    <div><svg class="icon" width="6" height="6" viewBox="0 0 10 10"><circle cx="5" cy="5" r="4.3" fill="none" stroke="var(--yellow)"/><path d="M0.7 5 H9.3 M5 0.7 Q2 5 5 9.3 M5 0.7 Q8 5 5 9.3" fill="none" stroke="var(--yellow)" stroke-width="0.8"/></svg>www.maplegrove-schools.com</div>
  </div>
  <div class="footer-text address">48 Linden Avenue, Suite 3<br>Fairview, OR 97024</div>
</section>

<!-- Presentation folder -->
<section class="sheet folder">
  <svg class="shape" width="345" height="437" viewBox="0 0 345 437">
    <path d="M0 0 H345 V42 Q200 112 0 105 Z" fill="var(--navy)" role="img" aria-label="Navy band with faint repeating star pattern"/>
    <path d="M0 107 Q200 114 345 46" fill="none" stroke="var(--yellow)" stroke-width="3.5"/>
    <path d="M0 392 Q150 335 345 339 V437 H0 Z" fill="var(--navy)" role="img" aria-label="Navy band with faint repeating star pattern"/>
    <path d="M0 388 Q150 331 250 334" fill="none" stroke="var(--yellow)" stroke-width="3.5"/>
  </svg>
  <div class="brand"><span class="brand-dot"></span>Maple Grove<br>Schools</div>
  <div class="tagline">Bright Futures Start Here</div>
</section>

<!-- Business card, front -->
<section class="sheet card-front">
  <svg class="shape" width="132" height="75" viewBox="0 0 132 75">
    <path d="M0 23 Q50 60 132 47 V75 H0 Z" fill="var(--navy)"/>
    <path d="M24 42 Q75 58 132 46" fill="none" stroke="#fff" stroke-width="1.2"/>
    <path d="M24 41 Q75 56 132 44" fill="none" stroke="var(--yellow)" stroke-width="1.4"/>
  </svg>
  <div class="person">
    <div class="person-name">DANIEL R. WHITCOMBE</div>
    <div class="person-role">Founder &amp; CEO</div>
  </div>
  <div class="brand"><span class="brand-dot"></span>Maple Grove<br>Schools</div>
  <div class="tagline">Bright Futures Start Here</div>
  <div class="footer-text contacts">
    <div>(555) 014-2290</div>
    <div>info@maplegrove-schools.com</div>
    <div>www.maplegrove-schools.com</div>
  </div>
  <div class="footer-text address">48 Linden Avenue, Suite 3<br>Fairview, OR 97024</div>
</section>

<!-- Business card, back -->
<section class="sheet card-back" role="img" aria-label="Navy card back with repeating star pattern"></section>

<!-- DL envelope, front -->
<section class="sheet envelope-front">
  <svg class="shape" width="328" height="157" viewBox="0 0 328 157">
    <path d="M0 78 Q160 152 328 104 V157 H0 Z" fill="var(--navy)"/>
    <path d="M98 113 Q220 135 328 102" fill="none" stroke="#fff" stroke-width="2"/>
    <path d="M98 110 Q220 131 328 99" fill="none" stroke="var(--yellow)" stroke-width="2.5"/>
  </svg>
  <div class="brand"><span class="brand-dot"></span>Maple Grove<br>Schools</div>
  <div class="tagline">Bright Futures Start Here</div>
  <div class="footer-text address">Maple Grove Schools<br>310 W Orchard Rd Suite<br>5 Brookdale, KS 66801</div>
</section>

<!-- DL envelope, back -->
<section class="sheet envelope-back">
  <svg class="shape" width="329" height="157" viewBox="0 0 329 157">
    <path d="M0 0 H329 L323 50 Q322 56 316 56 H13 Q7 56 6 50 Z" fill="var(--navy)"/>
  </svg>
  <div class="brand"><span class="brand-dot"></span>Maple Grove Schools</div>
</section>

</body>
</html>
```